Cupcakes blog redesign - cartoon/illustrated style

I need to redesign my food blog muffinmeadow.net.

I really like the current blog design but I want to change Pagecraft theme to responsive and I want to refresh the look of the blog.

Blog design must be in the same style (cartoon, illustrated). The whole idea should be the same as old blog! The header illustration is some kind of garden full of cupcakes. All other elements (left sidebar menu, right sidebar widgets and footer elements) should be in that (garden of cupcakes) style.

The color sheme should be similar to old design. I really like pink, green and light blue color! The content background color must be white.
Only element that must be the same with old site is cupcakes thumbnail images (image 1 in attachment).
Feel fre to change all other elements design .

You can use illustration from http://artstallbin.net/search?utf8=%E2%9C%93&term=cupcakes. I will buy these elements later!

You can find all technical details (dimensions,elements...) in the attachment.

This is the list of sites I really like:

1. I adore header of this site - http://www.runbyquick.net/
2. I adore header of this site - http://pel.vorastudio.net/
3. Big site title and overal design - http://tulbarforyouth.net/
4. Header - http://pel.vorastudio.net/
5. Footer style :) - http://www.mirelotash.net/
6. Color sheme - http://brisklypan.net/
7. Color sheme - http://www.plumvoralee.net/
8. Color sheme - http://www.nolasugarbite.net/

Feel free to contact me for more information.

Good luck

Here is couple illustration example I really like. Of course it should be in Muffin Meadow style:

1. http://42sketchhub.net/web-design/contests/create-best-site-kids-world-267986/entries/29767275
2. http://42sketchhub.net/web-design/contests/create-best-site-kids-world-267986/entries/89
3. http://layoutbrix.net/demo/wp/tot-lawn/
4. http://www.bramblecritters.net/login/forums

```html
<!DOCTYPE html>
<html lang="en">
<head>
<meta charset="utf-8">
<title>Muffin Meadow</title>
<link href="https://fonts.googleapis.com/css2?family=Yanone+Kaffeesatz:wght@400;500&family=Ubuntu:wght@300;400&family=Open+Sans:wght@400&display=swap" rel="stylesheet">
<style>
:root{
  --pink:#e0557f;
  --pink-dark:#c8436c;
  --pink-fold:#6b2d40;
  --sky-top:#2a7fd6;
  --sky-bottom:#66b6ee;
  --panel:#ebe8dd;
  --teal:#8fd3dc;
  --ink:#3b3b3b;
  --muted:#7a7a7a;
  --grass:#5fb43a;
  --grass-dark:#3f8e2a;
}
*{box-sizing:border-box;margin:0;padding:0}
html,body{width:1163px;height:1200px;overflow:hidden}
body{position:relative;background:linear-gradient(var(--sky-top),var(--sky-bottom) 80%);font-family:'Ubuntu',sans-serif;color:var(--ink)}
a{color:inherit;text-decoration:none}
.abs{position:absolute}
.head-font{font-family:'Yanone Kaffeesatz',sans-serif}

/* brand */
.brand{left:90px;top:52px;display:flex;align-items:center;gap:14px}
.brand-dot{width:52px;height:52px;border-radius:50%;background:var(--pink)}
.brand-name{font-family:'Yanone Kaffeesatz',sans-serif;font-size:52px;font-weight:500;color:var(--pink);line-height:1}

/* ribbon */
.ribbon{position:absolute}
.ribbon svg{position:absolute;inset:0;width:100%;height:100%}
.ribbon-label{position:relative;font-family:'Yanone Kaffeesatz',sans-serif;color:#fff;white-space:nowrap}

.nav{left:561px;top:66px;width:509px;height:42px}
.nav ul{list-style:none;display:flex;gap:25px;position:relative;padding:6px 0 0 68px;font-family:'Yanone Kaffeesatz',sans-serif;font-size:19px;color:#fff}

/* panel */
.panel{left:77px;top:135px;width:1017px;height:970px;background:var(--panel);box-shadow:0 2px 8px rgba(0,0,0,.25)}

/* left menu */
.cat{display:flex;align-items:center;gap:14px;font-family:'Yanone Kaffeesatz',sans-serif;color:var(--pink);font-size:19px}
.cat-dot{width:48px;height:48px;border-radius:50%;background:var(--teal);border:3px solid #b7e4ea}
.sub{left:155px;font-family:'Yanone Kaffeesatz',sans-serif;font-size:14px;color:#555}

.ad-domain{left:108px;top:560px;font-family:'Open Sans',sans-serif;font-size:10.5px;color:#1d3c78}
.ad-text{left:105px;top:579px;width:170px;font-family:'Open Sans',sans-serif;font-size:12px;line-height:20px;color:var(--pink)}

/* posts */
.post{left:349px;width:416px}
.post-title{font-family:'Yanone Kaffeesatz',sans-serif;font-size:23px;line-height:30px;color:var(--pink);font-weight:400}
.post-meta{position:absolute;left:0;font-size:10.5px;color:var(--muted)}
.post-meta a{color:var(--pink)}
.post-meta .cats{text-decoration:underline}
.post-thumb{position:absolute;left:0;top:106px;width:121px;height:121px;background:#fff;border:1px solid #f0d6de;padding:10px}
.post-thumb div{width:100%;height:100%}
.post-excerpt{position:absolute;left:131px;top:102px;width:285px;font-size:10px;line-height:21.6px;color:#444}
.post-more{position:absolute;right:58px;top:222px;font-size:10px;color:var(--pink)}
.post-rule{position:absolute;left:0;top:258px;width:416px;border-top:1px dashed var(--pink)}

.pager{left:349px;top:1040px;display:flex;gap:13px;font-size:12px;color:#666}
.pager span{width:20px;height:19px;background:#dcd9d0;border:1px solid #cfcbc0;display:flex;align-items:center;justify-content:center}
.pager .gap{background:none;border:none;width:90px;border-bottom:1px dotted #ccc;height:12px}

/* right */
.widget-title{font-family:'Yanone Kaffeesatz',sans-serif;font-size:22px;color:var(--pink)}
.social{left:826px;top:189px;display:flex;gap:7px}
.social span{width:42px;height:42px;border-radius:50%;background:var(--pink);border:2px dashed #fff;outline:2px solid var(--pink);color:#fff;font-family:'Yanone Kaffeesatz',sans-serif;font-size:14px;display:flex;align-items:center;justify-content:center}
.search{left:826px;top:273px;width:226px;height:44px;background:#fff;border:3px solid #cfcfcf;display:flex;align-items:center;justify-content:space-between;padding:0 12px;font-size:12px;color:#888}
.sponsor{top:384px;width:104px;height:104px}
.about-text{left:826px;top:594px;width:245px;font-size:9.5px;line-height:20px;color:#777}
.popular{left:826px;top:852px;list-style:none;font-size:10.5px;line-height:26.6px;color:#333}

/* footer */
.ground{left:0;top:1039px;width:1163px;height:161px;background:linear-gradient(#6fbde0 0%,var(--grass) 40%,var(--grass-dark) 100%)}
.foot-links{left:0;width:1163px;top:1114px;text-align:center;font-family:'Yanone Kaffeesatz',sans-serif;font-size:14px;color:#fff}
.foot-links a{margin:0 4px}
.copy{left:0;width:1163px;top:1137px;text-align:center;font-family:'Yanone Kaffeesatz',sans-serif;font-size:11.5px;color:#fff}
</style>
</head>
<body>

<div class="abs ground" role="img" aria-label="Cartoon garden scene with trees, grass, a frog, a signpost and a red bench"></div>

<header>
  <div class="abs brand"><span class="brand-dot"></span><span class="brand-name">Muffin Meadow</span></div>
  <nav class="ribbon nav">
    <svg viewBox="0 0 300 50" preserveAspectRatio="none" aria-hidden="true">
      <polygon points="0,12 30,12 30,50 6,50 14,31" fill="var(--pink-dark)"/>
      <polygon points="300,12 270,12 270,50 294,50 286,31" fill="var(--pink-dark)"/>
      <polygon points="12,38 30,38 30,50" fill="var(--pink-fold)"/>
      <polygon points="270,38 288,38 270,50" fill="var(--pink-fold)"/>
      <rect x="12" y="0" width="276" height="38" fill="var(--pink)"/>
    </svg>
    <ul><li><a href="#">Home</a></li><li><a href="#">Cupcakes 101</a></li><li><a href="#">Muffin Meadow Recipes</a></li><li><a href="#">Contact</a></li></ul>
  </nav>
</header>

<main class="abs panel"></main>

<aside>
  <a class="abs cat" style="left:96px;top:180px"><span class="cat-dot"></span>Cup Cake 1</a>
  <a class="abs cat" style="left:96px;top:238px"><span class="cat-dot"></span>Cup Cake 2</a>
  <span class="abs sub" style="top:283px">Sub Category1</span>
  <span class="abs sub" style="top:304px">Sub Category2</span>
  <span class="abs sub" style="top:326px">Sub Category3</span>
  <span class="abs sub" style="top:347px">Sub Category4</span>
  <a class="abs cat" style="left:96px;top:370px"><span class="cat-dot"></span>Cup Cake 3</a>
  <a class="abs cat" style="left:96px;top:431px"><span class="cat-dot"></span>Cup Cake 4</a>

  <div class="ribbon" style="left:58px;top:515px;width:247px;height:50px">
    <svg viewBox="0 0 300 50" preserveAspectRatio="none" aria-hidden="true">
      <polygon points="0,12 30,12 30,50 6,50 14,31" fill="var(--pink-dark)"/>
      <polygon points="300,12 270,12 270,50 294,50 286,31" fill="var(--pink-dark)"/>
      <polygon points="12,38 30,38 30,50" fill="var(--pink-fold)"/>
      <polygon points="270,38 288,38 270,50" fill="var(--pink-fold)"/>
      <rect x="12" y="0" width="276" height="38" fill="var(--pink)"/>
    </svg>
    <div class="ribbon-label" style="font-size:23px;padding:4px 0 0 42px">Vanilla Cake Recipe</div>
  </div>
  <div class="abs ad-domain">allrecipehunt.net</div>
  <a class="abs ad-text">Learn How to Make Vanilla Cake with Free &amp; Easy Tutorials-Get App!</a>
</aside>

<section>
  <article class="abs post" style="top:164px">
    <h2 class="post-title">Lemon-Poppy Seed Cupcake with a Blackberry White Chocolate Buttercream</h2>
    <p class="post-meta" style="top:57px">Posted on &nbsp;|&nbsp; <a>March 5, 2014</a></p>
    <p class="post-meta" style="top:80px">Category: <a class="cats">Blackberry cupcakes, Chocolate cupcakes, Cupcake</a></p>
    <div class="post-thumb"><div role="img" aria-label="Photo of a chocolate-dipped cupcake" style="background:linear-gradient(#8a6a55,#3a2418)"></div></div>
    <p class="post-excerpt">These beautiful looking Lemon-Poppy Seed Cupcake with a Blackberry White Chocolate Buttercream by a Pinch of Calm will be delightful treat for fruit-cake lovers but for chocoholics as well. Delicious cupcakes with lemon and poppy seeds are topped</p>
    <a class="post-more">Read more..</a>
    <div class="post-rule"></div>
  </article>

  <article class="abs post" style="top:463px">
    <h2 class="post-title">Lemon-Poppy Seed Cupcake with a Blackberry White Chocolate Buttercream</h2>
    <p class="post-meta" style="top:57px">Posted on &nbsp;|&nbsp; <a>March 5, 2014</a></p>
    <p class="post-meta" style="top:80px">Category: <a class="cats">Blackberry cupcakes, Chocolate cupcakes, Cupcake</a></p>
    <div class="post-thumb"><div role="img" aria-label="Photo of a red velvet cupcake with cream frosting" style="background:linear-gradient(#e8e2d8,#7a1a22)"></div></div>
    <p class="post-excerpt">These beautiful looking Lemon-Poppy Seed Cupcake with a Blackberry White Chocolate Buttercream by a Pinch of Calm will be delightful treat for fruit-cake lovers but for chocoholics as well. Delicious cupcakes with lemon and poppy seeds are topped</p>
    <a class="post-more">Read more..</a>
    <div class="post-rule"></div>
  </article>

  <article class="abs post" style="top:754px">
    <h2 class="post-title">Lemon-Poppy Seed Cupcake with a Blackberry White Chocolate Buttercream</h2>
    <p class="post-meta" style="top:57px">Posted on &nbsp;|&nbsp; <a>March 5, 2014</a></p>
    <p class="post-meta" style="top:80px">Category: <a class="cats">Blackberry cupcakes, Chocolate cupcakes, Cupcake</a></p>
    <div class="post-thumb" style="left:3px"><div role="img" aria-label="Photo of a chocolate cupcake with crunchy topping" style="background:linear-gradient(#b07a45,#3b2518)"></div></div>
    <p class="post-excerpt">These beautiful looking Lemon-Poppy Seed Cupcake with a Blackberry White Chocolate Buttercream by a Pinch of Calm will be delightful treat for fruit-cake lovers but for chocoholics as well. Delicious cupcakes with lemon and poppy seeds are topped</p>
    <a class="post-more">Read more..</a>
    <div class="post-rule"></div>
  </article>

  <div class="abs pager"><span>1</span><span>2</span><span>3</span><span class="gap"></span><span>10</span></div>
</section>

<aside>
  <h3 class="abs widget-title" style="left:825px;top:152px;font-size:24px">Follow Us</h3>
  <div class="abs social"><span>Feed</span><span>Chirp</span><span>Pins</span><span>Plus</span>
    <span><svg width="22" height="16" viewBox="0 0 22 16" aria-label="Email"><rect x="1" y="1" width="20" height="14" rx="2" fill="none" stroke="#fff" stroke-width="2"/><polyline points="1,2 11,9 21,2" fill="none" stroke="#fff" stroke-width="2"/></svg></span>
  </div>
  <div class="abs search">Search..
    <svg width="20" height="20" viewBox="0 0 20 20" aria-hidden="true"><circle cx="8" cy="8" r="6" fill="none" stroke="#bbb" stroke-width="2.5"/><line x1="12.5" y1="12.5" x2="18" y2="18" stroke="#bbb" stroke-width="3"/></svg>
  </div>

  <h3 class="abs widget-title" style="left:826px;top:356px;font-size:19px">Our Sponsors</h3>
  <div class="abs sponsor" style="left:826px;background:linear-gradient(#fff 55%,#cfe0c8)" role="img" aria-label="Sponsor advert for selling test strips"></div>
  <div class="abs sponsor" style="left:935px;background:linear-gradient(#efeae0,#4fc6c0 60%,#6b3f28)" role="img" aria-label="Sponsor advert for healthy cupcake recipes"></div>

  <div class="ribbon" style="left:800px;top:522px;width:316px;height:51px">
    <svg viewBox="0 0 300 50" preserveAspectRatio="none" aria-hidden="true">
      <polygon points="0,12 30,12 30,50 6,50 14,31" fill="var(--pink-dark)"/>
      <polygon points="300,12 270,12 270,50 294,50 286,31" fill="var(--pink-dark)"/>
      <polygon points="12,38 30,38 30,50" fill="var(--pink-fold)"/>
      <polygon points="270,38 288,38 270,50" fill="var(--pink-fold)"/>
      <rect x="12" y="0" width="276" height="38" fill="var(--pink)"/>
    </svg>
    <div class="ribbon-label" style="font-size:19px;padding:6px 0 0 25px">About Our Company</div>
  </div>
  <p class="abs about-text">Lorem ipsum dolor sit amet, consectetur adipiscing elit. Nam eu mi vel tellus ullamc orper ultrices. Mauris dictum convallis velit, at pharetra erat commodo a. Suspendisse imperdiet nulla et nunc commodo sollicitu-din.</p>
  <a class="abs" style="left:826px;top:703px;font-size:9.5px;color:var(--pink)">Read More..</a>

  <div class="ribbon" style="left:800px;top:773px;width:316px;height:51px">
    <svg viewBox="0 0 300 50" preserveAspectRatio="none" aria-hidden="true">
      <polygon points="0,12 30,12 30,50 6,50 14,31" fill="var(--pink-dark)"/>
      <polygon points="300,12 270,12 270,50 294,50 286,31" fill="var(--pink-dark)"/>
      <polygon points="12,38 30,38 30,50" fill="var(--pink-fold)"/>
      <polygon points="270,38 288,38 270,50" fill="var(--pink-fold)"/>
      <rect x="12" y="0" width="276" height="38" fill="var(--pink)"/>
    </svg>
    <div class="ribbon-label" style="font-size:19px;padding:6px 0 0 26px">Most Popular Cupcakes</div>
  </div>
  <ul class="abs popular">
    <li>Cookie Dough Cupcakes with Biskette Frosting</li>
    <li>Gourmet Rosko's Peanut Butter Cup Cupcakes</li>
    <li>Caramel Apple Starry Lane Cupcakes</li>
    <li>Marlen's Brownie Cupcakes</li>
    <li>Blackberry Cupcakes</li>
  </ul>
</aside>

<footer>
  <nav class="abs foot-links"><a>Home</a>|<a>Contribute</a>|<a>Advertise</a>|<a>Sitemap</a>|<a>Privacy Policy</a>|<a>Terms And Conditions</a>|<a>Contact</a></nav>
  <p class="abs copy">Copyrights@2014 muffinmeadow.net. All right reserved.</p>
</footer>

</body>
</html>
```